Business Card: RW Office Partners - Your organised problem solver

Business Name: RW Office Partners
Website: www.rwofficepartners.com.au
Email: marisol@rwofficepartners.com.au
Mobile: 61 482 907 236
Facebook: @rwofficepartners
Instrgram: @rwofficepartners

Brading Colours:
HEX
#986474
#ddccd3
#7a8498
#c9d8e4
#000000
#ffffff

Tag Line: Your organised problem solver

Link to DRAFT website:
https://deskhelpcollective.wixsite.com/rw-office-partners

About Page from the website:
My name is Marisol Wrenfield, and I would love to assist you to become more productive in your day to day and achieve your business and personal goals.
My mission is to give you time, time to work on the important tasks of your business or to be able to spend more time with your family. I will take on the tasks you don’t have time for, don’t know well or simply don’t like to do.
I have an extensive background in Administration, Tender Coordination, Document Control, WHS and Quality Management working primarily in the Construction, Mining and Corporate World.
I am passionate about being organised, having order and making things in your life (and mine) easier! I love to watch something unfold and grow into something amazing! I am known for being the go-to problem solver, the organiser of all things, producing high standards of work even under pressure. I’m also a confident communicator, and I understand that you’re busy running your business.

Target Market(s)

Small to Medium Business who require assistance in their business by a virtual assistant.

Industry/Entity Type

Virtual Assistant

Contact Information for Business Card

Mobile: 61 482 907 236

Font styles to use
Sans Serif

Colors
ffffff

Requirements
Must have
• Branding Colours as outlined.
Contact Details as outlined.
Logo as provided.
Proper contact details - mobile, facebook, instragm, website.
Simple, Elegant, very clean looking.
Should not have
• Note cute with pictures.
Not too girly as still want to market to construction companies.

```html
<!DOCTYPE html>
<html lang="en">
<head>
<meta charset="utf-8">
<title>RW Office Partners – Business Card</title>
<link href="https://fonts.googleapis.com/css2?family=Montserrat:wght@500;600&family=Roboto:wght@400&display=swap" rel="stylesheet">
<style>
  :root {
    --stage: #2a2a2c;
    --card: #1d1d1f;
    --card-pattern-a: #1f1f21;
    --card-pattern-b: #262628;
    --rose: #986474;
    --rose-light: #a8727f;
    --slate: #8a93a8;
    --slate-dark: #7a8498;
  }
  * { margin: 0; padding: 0; box-sizing: border-box; }
  html, body { width: 1200px; height: 900px; overflow: hidden; }
  body {
    background: var(--stage);
    display: flex;
    flex-direction: column;
    align-items: center;
    justify-content: center;
    gap: 40px;
  }
  .card {
    position: relative;
    width: 630px;
    height: 360px;
    border-radius: 4px;
    overflow: hidden;
    box-shadow: 0 10px 30px rgba(0,0,0,.45);
  }
  .card--front { background: var(--card); }
  .brand {
    position: absolute;
    left: 58px;
    top: 92px;
    display: flex;
    align-items: center;
    gap: 12px;
    font-family: "Montserrat", sans-serif;
    font-weight: 600;
    font-size: 27px;
    letter-spacing: .5px;
    color: var(--slate);
    text-transform: uppercase;
    line-height: 1.1;
  }
  .brand__mark {
    width: 16px; height: 16px;
    background: var(--rose);
    flex: none;
  }
  .divider {
    position: absolute;
    left: 325px;
    top: 150px;
    width: 2px;
    height: 92px;
    background: var(--rose);
  }
  .contact {
    position: absolute;
    left: 343px;
    top: 150px;
    list-style: none;
    font-family: "Roboto", sans-serif;
    font-size: 15.5px;
    color: var(--slate);
  }
  .contact__item {
    display: flex;
    align-items: center;
    gap: 8px;
    height: 23px;
  }
  .contact__icon { width: 13px; height: 13px; flex: none; fill: var(--slate-dark); }
  .contact__social { display: flex; gap: 4px; }
  .contact__social span { width: 11px; height: 11px; background: var(--slate-dark); border-radius: 2px; }
  .tagline {
    position: absolute;
    left: 125px;
    top: 268px;
    font-family: "Roboto", sans-serif;
    font-size: 15.5px;
    color: var(--rose);
  }
  .card--back {
    background: linear-gradient(135deg, var(--card-pattern-b), var(--card-pattern-a));
  }
  .back__name {
    position: absolute;
    right: 40px;
    bottom: 34px;
    font-family: "Montserrat", sans-serif;
    font-weight: 600;
    font-size: 22px;
    color: var(--rose);
  }
</style>
</head>
<body>
  <section class="card card--front">
    <div class="brand">
      <span class="brand__mark"></span>
      <span class="brand__name">RW Office Partners</span>
    </div>
    <div class="divider"></div>
    <ul class="contact">
      <li class="contact__item">
        <svg class="contact__icon" viewBox="0 0 16 16"><path d="M3.6 1.5l2.3 2.7-1.3 1.6c.9 2 2.5 3.6 4.6 4.6l1.6-1.3 2.7 2.3-1.3 2.1C7 13.2 2.8 9 1.5 2.8z"/></svg>
        61 482 907 236
      </li>
      <li class="contact__item">
        <svg class="contact__icon" viewBox="0 0 16 16"><path d="M1 3h14v1.2L8 9 1 4.2zM1 6l7 4.8L15 6v7H1z"/></svg>
        marisol@rwofficepartners.com.au
      </li>
      <li class="contact__item">
        <svg class="contact__icon" viewBox="0 0 16 16"><circle cx="8" cy="8" r="7"/></svg>
        www.rwofficepartners.com.au
      </li>
      <li class="contact__item">
        <span class="contact__social"><span></span><span></span></span>
        @rwofficepartners
      </li>
    </ul>
    <p class="tagline">Your organised problem solver</p>
  </section>

  <section class="card card--back" role="img" aria-label="Tone-on-tone monogram pattern across the card back">
    <span class="back__name">RW Office Partners</span>
  </section>
</body>
</html>
```